Harborlight Amusement Collective (HAC)

We need a business card design for Harborlight Amusement Collective. Modern and sleek looking, with all critical information. Open to single or double sided designs, if double sided info needs to be all on one side. The main Logo is Harborlight Amusement collective and must be on the card. The other three logos are for the brands that fall under the group, they might be good on the back.

Industry/Entity Type

Business

```html
<!DOCTYPE html>
<html lang="en">
<head>
<meta charset="utf-8">
<title>Harborlight Amusement Collective – Business Card</title>
<link href="https://fonts.googleapis.com/css2?family=Montserrat:wght@500;600;700&family=Lato:wght@400;700&display=swap" rel="stylesheet">
<style>
  :root {
    --page-bg: #e2e2e2;
    --card-white: #ffffff;
    --brand-blue: #23579b;
    --brand-green: #7f9f2a;
    --ink: #2e2e2e;
  }
  * { box-sizing: border-box; margin: 0; padding: 0; }
  html, body { width: 1200px; height: 900px; overflow: hidden; }
  body { background: var(--page-bg); position: relative; font-family: "Lato", Arial, sans-serif; color: var(--ink); }

  .card { position: absolute; top: 306px; width: 440px; height: 271px; overflow: hidden; }
  .card-front { left: 149px; background: var(--card-white); }
  .card-back { left: 608px; background: var(--brand-blue); }

  /* front */
  .front-band { position: absolute; top: 0; right: 0; width: 78px; height: 100%; background: var(--brand-blue); }
  .front-mark {
    position: absolute; left: 312px; top: 84px; width: 104px; height: 104px;
    background: var(--card-white); border: 3px solid var(--brand-blue);
    display: flex; align-items: center; justify-content: center;
    font-family: "Montserrat", sans-serif; font-weight: 700; font-size: 30px;
    color: var(--brand-blue); letter-spacing: 2px;
  }
  .company-name {
    position: absolute; left: 21px; top: 34px; width: 290px;
    font-family: "Montserrat", sans-serif; font-weight: 700; color: var(--brand-blue);
    text-align: center; line-height: 1.15;
  }
  .company-name .line-main { display: block; font-size: 15.5px; letter-spacing: 0.2px; }
  .company-name .line-sub { display: block; font-size: 16px; letter-spacing: 7px; margin-top: 6px; }

  .person { position: absolute; left: 22px; top: 111px; }
  .person-name { font-family: "Montserrat", sans-serif; font-weight: 500; font-size: 15px; color: var(--brand-blue); letter-spacing: 0.3px; }
  .person-name .surname { color: var(--brand-green); }
  .person-role { font-size: 11.5px; margin-top: 1px; }

  .contact-list { position: absolute; left: 22px; top: 151px; list-style: none; font-size: 11.5px; }
  .contact-list li { display: flex; align-items: center; height: 16px; }
  .contact-list svg { width: 10px; height: 10px; margin-right: 6px; fill: var(--brand-blue); }
  .address { position: absolute; left: 21px; top: 221px; font-size: 11.5px; line-height: 16px; }

  /* back */
  .back-mark {
    position: absolute; left: 183px; top: 40px; width: 74px; height: 74px;
    border: 3px solid var(--card-white);
    display: flex; align-items: center; justify-content: center;
    font-family: "Montserrat", sans-serif; font-weight: 700; font-size: 22px;
    color: var(--card-white); letter-spacing: 2px;
  }
  .back-name {
    position: absolute; left: 0; top: 134px; width: 100%; text-align: center;
    font-family: "Montserrat", sans-serif; font-weight: 700; color: var(--card-white); line-height: 1.15;
  }
  .back-name .line-main { display: block; font-size: 17px; }
  .back-name .line-sub { display: block; font-size: 16px; letter-spacing: 7px; margin-top: 8px; }

  .brand-strip {
    position: absolute; left: 0; bottom: 0; width: 100%; height: 66px; background: var(--card-white);
    display: flex; align-items: center; justify-content: space-around; padding: 0 18px;
  }
  .sub-brand { display: flex; align-items: center; font-family: "Montserrat", sans-serif; font-weight: 700; font-size: 13px; }
  .sub-brand .dot { width: 18px; height: 18px; border-radius: 50%; margin-right: 6px; }
  .sub-brand.bleacherview { color: var(--ink); }
  .sub-brand.bleacherview .dot { background: var(--ink); }
  .sub-brand.harbortix { color: var(--brand-green); }
  .sub-brand.harbortix .dot { background: var(--brand-green); border-radius: 3px; }
  .sub-brand.seatmark { color: var(--brand-blue); font-size: 16px; }
  .sub-brand.seatmark .dot { background: var(--brand-blue); width: 22px; height: 22px; }
</style>
</head>
<body>

<section class="card card-front" aria-label="Business card front">
  <div class="company-name">
    <span class="line-main">HARBORLIGHT AMUSEMENT</span>
    <span class="line-sub">COLLECTIVE</span>
  </div>

  <div class="person">
    <p class="person-name">DANIEL <span class="surname">MORROW</span></p>
    <p class="person-role">Managing Director</p>
  </div>

  <ul class="contact-list">
    <li><svg viewBox="0 0 10 10" aria-hidden="true"><path d="M1 3.5C1 2 2.5 1 5 1s4 1 4 2.5L7.4 4.3 6.6 3H3.4L2.6 4.3zM2.5 5h5l1 4h-7z"/></svg>044-987 654 321</li>
    <li><svg viewBox="0 0 10 10" aria-hidden="true"><path d="M3 0h4a1 1 0 0 1 1 1v8a1 1 0 0 1-1 1H3a1 1 0 0 1-1-1V1a1 1 0 0 1 1-1zm0 1.5v6h4v-6z"/></svg>044-555 210 846</li>
    <li><svg viewBox="0 0 10 10" aria-hidden="true"><path d="M0 2h10v1L5 6 0 3zm0 2.2 5 3 5-3V8H0z"/></svg>hello@harborlightac.com</li>
    <li><svg viewBox="0 0 10 10" aria-hidden="true"><circle cx="5" cy="5" r="4.5"/><path d="M2 4h6M2 6h6M5 .5c-2 2.5-2 6.5 0 9M5 .5c2 2.5 2 6.5 0 9" stroke="#fff" stroke-width=".7" fill="none"/></svg>www.harborlightac.com</li>
  </ul>

  <p class="address">48 Quayside Lane<br>Port Alden, 204519.</p>

  <div class="front-band"></div>
  <div class="front-mark">HAC</div>
</section>

<section class="card card-back" aria-label="Business card back">
  <div class="back-mark">HAC</div>
  <div class="back-name">
    <span class="line-main">HARBORLIGHT AMUSEMENT</span>
    <span class="line-sub">COLLECTIVE</span>
  </div>
  <div class="brand-strip">
    <span class="sub-brand bleacherview"><span class="dot"></span>Bleacherview</span>
    <span class="sub-brand harbortix"><span class="dot"></span>HarborTix</span>
    <span class="sub-brand seatmark"><span class="dot"></span>Seatmark</span>
  </div>
</section>

</body>
</html>
```